Hartwell Estates Business Cards

I would like a business card that includes myself and my partner.
Includes: Logo, office #, email, website, our names, our numbers and possibly the address. I would also like the logo to be embossed and the card to be horizontal.
There is a photo of our yard signs to give you an idea of the colors of our business.

Target Market(s)

Everyone in real estate market.
We are in a rural area. Our clientele are from all socioeconomic backgrounds.

Industry/Entity Type

Real Estate Agent

Contact Information for Business Card

Company Name: Hartwell Estates
Our Names, Titles & Cell #'s : Dana Pembrook-Broker (555).317.6624, Marla Pembrook-Realtor (555).609.1385
Office #: (555).240.3918
Website: hartwellestates-demo.com
Joint Email: pembrook@hartwellestates-demo.com
Office Address: 418B W. Calloway Ave.
Millbrook, OR. 70913

Font styles to use
Serif

Requirements
Must have
• HORIZONTAL, Logo, Myself and my partners names, Our cell #'s, our office #, our website, our email address
Nice to have
• Embossed logo, office address, our titles.

```html
<!DOCTYPE html>
<html lang="en">
<head>
<meta charset="utf-8">
<title>Hartwell Estates Business Cards</title>
<link rel="stylesheet" href="https://fonts.googleapis.com/css2?family=PT+Sans:wght@400;700&display=swap">
<style>
  :root {
    --stage: #2c2d30;
    --brand-purple: #4a1f6e;
    --card-white: #ffffff;
    --ink: #2a2a2a;
    --rule: #4a1f6e;
  }
  * { box-sizing: border-box; margin: 0; padding: 0; }
  html, body { width: 1200px; height: 864px; overflow: hidden; }
  body {
    background: var(--stage);
    font-family: "PT Sans", Arial, sans-serif;
    position: relative;
  }
  .card {
    position: absolute;
    left: 320px;
    width: 560px;
    height: 320px;
    border-radius: 3px;
  }
  .card--front {
    top: 80px;
    background: var(--brand-purple);
    display: flex;
    align-items: center;
    justify-content: center;
  }
  .card--back {
    top: 464px;
    background: var(--card-white);
    color: var(--ink);
  }
  .brand {
    display: flex;
    align-items: center;
    gap: 14px;
  }
  .brand__dot {
    width: 30px;
    height: 30px;
    border-radius: 50%;
  }
  .brand__name {
    font-weight: 700;
    font-size: 40px;
    letter-spacing: 0.5px;
    line-height: 1;
  }
  .card--front .brand__dot { background: var(--card-white); }
  .card--front .brand__name { color: var(--card-white); }
  .card--back .brand {
    position: absolute;
    top: 36px;
    left: 0;
    right: 0;
    justify-content: center;
  }
  .card--back .brand__dot { background: var(--brand-purple); }
  .card--back .brand__name { color: var(--brand-purple); font-size: 36px; }

  .agent {
    position: absolute;
    top: 118px;
    font-size: 13px;
    line-height: 1.3;
  }
  .agent__name {
    color: var(--brand-purple);
    font-weight: 700;
    font-size: 17px;
  }
  .agent--broker { left: 150px; text-align: right; }
  .agent--realtor { left: 306px; top: 132px; }
  .agent__phone { display: flex; align-items: center; gap: 6px; }
  .agent--broker .agent__phone { justify-content: flex-end; flex-direction: row-reverse; }

  .divider {
    position: absolute;
    left: 40px;
    right: 40px;
    top: 204px;
    height: 1px;
    background: var(--rule);
  }
  .contacts {
    position: absolute;
    left: 40px;
    top: 214px;
    list-style: none;
    font-size: 14px;
    line-height: 1.35;
  }
  .contacts li { display: flex; align-items: center; gap: 8px; }
  .address {
    position: absolute;
    right: 40px;
    top: 218px;
    text-align: right;
    font-style: normal;
    font-size: 14px;
    line-height: 1.4;
  }
  .icon { width: 11px; height: 11px; fill: var(--brand-purple); flex: none; }
</style>
</head>
<body>

<section class="card card--front" aria-label="Card front">
  <div class="brand">
    <span class="brand__dot"></span>
    <span class="brand__name">Hartwell Estates</span>
  </div>
</section>

<section class="card card--back" aria-label="Card back">
  <div class="brand">
    <span class="brand__dot"></span>
    <span class="brand__name">Hartwell Estates</span>
  </div>

  <div class="agent agent--broker">
    <div class="agent__name">Dana Pembrook</div>
    <div>Broker</div>
    <div class="agent__phone">
      <svg class="icon" viewBox="0 0 24 24"><path d="M6.6 10.8c1.4 2.8 3.8 5.1 6.6 6.6l2.2-2.2c.3-.3.7-.4 1-.2 1.1.4 2.3.6 3.6.6.6 0 1 .4 1 1V20c0 .6-.4 1-1 1C10.6 21 3 13.4 3 4c0-.6.4-1 1-1h3.5c.6 0 1 .4 1 1 0 1.3.2 2.5.6 3.6.1.3 0 .7-.2 1z"/></svg>
      <span>(555).317.6624</span>
    </div>
  </div>

  <div class="agent agent--realtor">
    <div class="agent__name">Marla Pembrook</div>
    <div>Realtor</div>
    <div class="agent__phone">
      <svg class="icon" viewBox="0 0 24 24"><path d="M6.6 10.8c1.4 2.8 3.8 5.1 6.6 6.6l2.2-2.2c.3-.3.7-.4 1-.2 1.1.4 2.3.6 3.6.6.6 0 1 .4 1 1V20c0 .6-.4 1-1 1C10.6 21 3 13.4 3 4c0-.6.4-1 1-1h3.5c.6 0 1 .4 1 1 0 1.3.2 2.5.6 3.6.1.3 0 .7-.2 1z"/></svg>
      <span>(555).609.1385</span>
    </div>
  </div>

  <div class="divider"></div>

  <ul class="contacts">
    <li>
      <svg class="icon" viewBox="0 0 24 24"><path d="M6.6 10.8c1.4 2.8 3.8 5.1 6.6 6.6l2.2-2.2c.3-.3.7-.4 1-.2 1.1.4 2.3.6 3.6.6.6 0 1 .4 1 1V20c0 .6-.4 1-1 1C10.6 21 3 13.4 3 4c0-.6.4-1 1-1h3.5c.6 0 1 .4 1 1 0 1.3.2 2.5.6 3.6.1.3 0 .7-.2 1z"/></svg>
      <span>(555).240.3918</span>
    </li>
    <li>
      <svg class="icon" viewBox="0 0 24 24"><path d="M2 5h20v14H2z"/><path d="M3 6l9 7 9-7" fill="none" stroke="#fff" stroke-width="1.6"/></svg>
      <span>pembrook@hartwellestates-demo.com</span>
    </li>
    <li>
      <svg class="icon" viewBox="0 0 24 24"><circle cx="12" cy="12" r="10"/><path d="M2 12h20M12 2c3 3 3 17 0 20M12 2c-3 3-3 17 0 20" fill="none" stroke="#fff" stroke-width="1.4"/></svg>
      <span>hartwellestates-demo.com</span>
    </li>
  </ul>

  <address class="address">
    418B W. Calloway Ave.<br>
    Millbrook,<br>
    OR. 70913
  </address>
</section>

</body>
</html>
```